Flight school sign for building, banner, and bilboard

This sign is primarily for use on the side of our flight school building to draw attention for current and future flight school students. We offer airplane and helicopter flight training, ground school training and seminars, airplane and helicopter rentals, multi-engine training, and more. I would like a professional but exciting sign that can be used across a multitude of signage options such as banners, banner ads, billboard, and other mediums so that our sign is consistent and recognizable.

Contact Information for Business Card

The business card should match our company sign somewhat but not exactly. We want good and exciting imagery or wording and energizing/exciting colors.

```html
<!DOCTYPE html>
<html lang="en">
<head>
<meta charset="utf-8">
<title>Zenith Aviation – Flight School Sign</title>
<link rel="stylesheet" href="https://fonts.googleapis.com/css2?family=Barlow+Semi+Condensed:wght@600;700;800&display=swap">
<style>
  :root {
    --sky-deep: #4fa9e2;
    --sky-light: #e4f3fc;
    --brand-red: #ec2434;
    --brand-navy: #232a66;
    --photo-light: #eef1f5;
    --photo-mid: #b9c2ce;
    --photo-dark: #6c7a90;
    --white: #ffffff;
    --stage-dark: #262626;
    --stage-light: #6b6b6b;
  }
  * { margin: 0; padding: 0; box-sizing: border-box; }
  html, body { width: 1000px; height: 1200px; overflow: hidden; }
  body {
    background: radial-gradient(ellipse at 80% 40%, var(--stage-light), var(--stage-dark) 75%);
    font-family: "Barlow Semi Condensed", "Arial Narrow", sans-serif;
  }
  .sign {
    position: absolute;
    left: 30px; top: 436px;
    width: 940px; height: 328px;
    overflow: hidden;
    box-shadow: 0 12px 30px rgba(0,0,0,.55);
  }
  .sign-inner {
    position: absolute; left: 0; top: 0;
    width: 1540px; height: 538px;
    transform: scale(0.6104);
    transform-origin: 0 0;
  }
  .sign-shapes { position: absolute; inset: 0; }
  .pilot-photo {
    position: absolute;
    left: 420px; top: 130px; width: 780px; height: 330px;
    background: linear-gradient(160deg, var(--photo-light) 0%, var(--photo-mid) 45%, var(--photo-dark) 100%);
    -webkit-mask-image: radial-gradient(ellipse 60% 70% at 55% 65%, #000 55%, transparent 100%);
    mask-image: radial-gradient(ellipse 60% 70% at 55% 65%, #000 55%, transparent 100%);
  }
  .headline {
    position: absolute; left: 64px; top: 48px;
    font-weight: 800; text-transform: uppercase; line-height: .86;
  }
  .headline-lead { display: block; color: var(--brand-navy); font-size: 80px; letter-spacing: 1px; }
  .headline-main { display: block; color: var(--brand-red); font-size: 130px; letter-spacing: 1px; }
  .brand-mark {
    position: absolute; left: 247px; top: 290px;
    width: 130px; height: 130px; border-radius: 50%;
    background: var(--brand-navy);
  }
  .brand-name {
    position: absolute; left: 68px; top: 454px;
    color: var(--brand-red); font-weight: 700; font-size: 46px;
    letter-spacing: 8px; text-transform: uppercase;
  }
  .services { list-style: none; }
  .service {
    position: absolute; display: flex; align-items: center;
    color: var(--white); font-weight: 700; font-size: 32px;
    line-height: 1.2; letter-spacing: .5px; text-transform: uppercase;
  }
  .service-icon { width: 70px; height: 70px; margin-right: 22px; flex: none; }
  .service-text { border-left: 2px solid var(--white); padding-left: 14px; }
  .service--training { left: 854px; top: 38px; }
  .service--ground { left: 918px; top: 138px; }
  .service--rentals { left: 986px; top: 238px; }
  .service--multi { left: 1053px; top: 337px; }
  .contact {
    position: absolute; top: 460px;
    display: flex; align-items: center; gap: 14px;
    color: var(--white); font-weight: 600; font-size: 50px;
  }
  .contact svg { width: 42px; height: 42px; }
  .contact--web { left: 612px; }
  .contact--phone { left: 1118px; }
</style>
</head>
<body>
  <div class="sign">
    <div class="sign-inner">
      <svg class="sign-shapes" viewBox="0 0 1540 538" width="1540" height="538" aria-hidden="true">
        <defs>
          <linearGradient id="sky" x1="0" y1="0" x2="0.5" y2="1">
            <stop offset="0" stop-color="var(--sky-deep)"/>
            <stop offset="1" stop-color="var(--sky-light)"/>
          </linearGradient>
        </defs>
        <rect class="sky" width="1540" height="538" fill="url(#sky)"/>
      </svg>

      <div class="pilot-photo" role="img" aria-label="Photo of a smiling pilot wearing a headset in the open cockpit of a small white training airplane"></div>

      <svg class="sign-shapes" viewBox="0 0 1540 538" width="1540" height="538" aria-hidden="true">
        <path class="panel-red" fill="var(--brand-red)" d="M650 0 L1540 0 L1540 446 L1160 446 C1040 446 980 390 915 265 C855 150 790 0 650 0 Z"/>
        <path class="corner-navy" fill="var(--brand-navy)" d="M1285 0 L1540 0 L1540 165 C1470 110 1380 50 1285 0 Z"/>
        <rect class="rule-white" x="1100" y="446" width="440" height="5" fill="var(--white)"/>
        <path class="band-light" fill="#f3f8fc" d="M40 451 L625 451 L565 538 L0 538 L0 470 Z"/>
        <path class="band-navy" fill="var(--brand-navy)" d="M625 451 L1130 451 C1110 451 1090 538 1060 538 L565 538 C590 520 600 451 625 451 Z"/>
        <path class="band-red" fill="var(--brand-red)" d="M1130 451 L1540 451 L1540 538 L1060 538 C1090 538 1110 451 1130 451 Z"/>
        <path class="corner-red" fill="var(--brand-red)" d="M0 452 C25 462 45 500 75 538 L0 538 Z"/>
        <rect class="edge-red" x="0" y="532" width="1540" height="6" fill="var(--brand-red)"/>
      </svg>

      <h1 class="headline">
        <span class="headline-lead">Excellence in</span>
        <span class="headline-main">Aviation</span>
      </h1>

      <div class="brand-mark" aria-hidden="true"></div>
      <div class="brand-name">Zenith Aviation</div>

      <ul class="services">
        <li class="service service--training">
          <svg class="service-icon" viewBox="0 0 70 70" fill="none" stroke="#fff" stroke-width="3" stroke-linejoin="round">
            <path d="M35 8 L35 62 M12 30 L58 30 L58 38 L12 38 Z M26 56 L44 56 M30 8 Q35 2 40 8"/>
          </svg>
          <span class="service-text">Airplane and<br>Helicopter flight training</span>
        </li>
        <li class="service service--ground">
          <svg class="service-icon" viewBox="0 0 70 70" fill="none" stroke="#fff" stroke-width="3">
            <rect x="24" y="6" width="40" height="26"/>
            <path d="M30 26 L40 18 L48 22 L58 12"/>
            <circle cx="12" cy="20" r="5"/><path d="M6 50 L6 32 L18 32 L18 50"/>
            <circle cx="30" cy="48" r="4"/><circle cx="44" cy="48" r="4"/><circle cx="58" cy="48" r="4"/>
            <path d="M24 62 Q30 54 36 62 M38 62 Q44 54 50 62 M52 62 Q58 54 64 62"/>
          </svg>
          <span class="service-text">Ground school<br>training and seminars</span>
        </li>
        <li class="service service--rentals">
          <svg class="service-icon" viewBox="0 0 70 70" fill="none" stroke="#fff" stroke-width="3" stroke-linejoin="round">
            <path d="M10 14 L60 14 M35 14 L35 22"/>
            <path d="M20 30 Q22 22 34 22 L46 22 Q56 24 56 38 Q56 48 44 48 L28 48 Q20 48 20 38 Z"/>
            <path d="M20 34 L4 30 L4 40 L20 40 M30 56 L54 56 M34 48 L34 56 M48 48 L48 56"/>
          </svg>
          <span class="service-text">Airplane and<br>helicopter rentals</span>
        </li>
        <li class="service service--multi">
          <svg class="service-icon" viewBox="0 0 70 70" fill="none" stroke="#fff" stroke-width="3">
            <circle cx="35" cy="37" r="26"/><circle cx="35" cy="37" r="6"/>
            <path d="M35 31 L35 13 M40 40 L56 48 M30 40 L14 48 M28 8 L42 8"/>
          </svg>
          <span class="service-text">Multi-engine training,<br>and more.</span>
        </li>
      </ul>

      <div class="contact contact--web">
        <svg viewBox="0 0 40 40" fill="none" stroke="#fff" stroke-width="2.5">
          <circle cx="20" cy="20" r="17"/><ellipse cx="20" cy="20" rx="8" ry="17"/>
          <path d="M3 20 L37 20 M6 11 L34 11 M6 29 L34 29"/>
        </svg>
        <span>ZenithAviation.com</span>
      </div>
      <div class="contact contact--phone">
        <svg viewBox="0 0 40 40" fill="none" stroke="#fff" stroke-width="2.5">
          <circle cx="20" cy="20" r="17"/>
          <path d="M14 11 L17 11 L19 16 L16.5 18 Q19 23 22 23.5 L24 21 L29 23 L29 26 Q27 29 23 28 Q13 25 11 15 Q11 12 14 11 Z"/>
        </svg>
        <span>(205) 555 0147</span>
      </div>
    </div>
  </div>
</body>
</html>
```